Harborview Optical -Window Poster (Optometrist)

We are an optometry practice and we need a poster for a new store promotion for our window highlighting we now also sell 2 pairs of glasses as a package deal. The size will be 1300mm width x 1900mm height

The artwork will be displayed as a fabric banner in our shop window. We have 7 other banners with different services our business provides. The words needs to standout for passers by and the cars stopped at the traffic lights out front of our business. We already have signs with our logos phone number etc. so we won't need them included in the poster.

It would need to include the following information.

Two pair packages now available*

*Conditions apply

The artwork will be displayed as a fabric banner in our shop window. We have 7 other banners with different services our business provides. The words needs to standout for passers by and the cars stopped at the traffic lights out front of our business. We already have signs with our logos phone number etc. so we won't need them included in the poster. Thank you for your work it's amazing Added Saturday, February 18, 2017

The artwork will be displayed as a fabric banner in our shop window. We have 7 other banners with different services our business provides. The words needs to standout for passers by and the cars stopped at the traffic lights out front of our business. We already have signs with our logos phone number etc. so we won't need them included in the poster. Added Saturday, February 18, 2017

Target Market(s)

Cars driving past and stopped at traffic lights outside our store.

Industry/Entity Type

Optician

Requirements
Must have
• Poster must say:
• Two pair packages now available*
• *Conditions apply

```html
<!DOCTYPE html>
<html lang="en">
<head>
<meta charset="utf-8">
<title>Harborview Optical – Two Pair Packages Window Poster</title>
<link rel="stylesheet" href="https://fonts.googleapis.com/css2?family=Bebas+Neue&family=Montserrat:wght@700;900&display=swap">
<style>
  :root {
    --ink-navy: #0d0a26;
    --band-navy: #0b0820;
    --flash-yellow: #f4e800;
    --deal-orange: #e08a1e;
    --paper-white: #ffffff;
    --sky-top: #a9a6b4;
    --sky-mid: #c7b3b0;
    --glow-peach: #e8c8a8;
    --city-mauve: #8a7c96;
    --city-dusk: #6f6885;
    --disc-light: #e0483a;
    --disc-deep: #cf3a30;
  }
  * { margin: 0; padding: 0; box-sizing: border-box; }
  html, body {
    width: 962px;
    height: 1200px;
    overflow: hidden;
    background: var(--paper-white);
  }
  .poster {
    position: relative;
    width: 962px;
    height: 1200px;
    overflow: hidden;
    font-family: "Montserrat", sans-serif;
  }
  .backdrop-scene {
    position: absolute;
    inset: 0;
    background: linear-gradient(180deg, var(--sky-top) 0%, var(--sky-mid) 40%, var(--glow-peach) 62%, var(--city-mauve) 80%, var(--city-dusk) 100%);
  }
  .eye-photo {
    position: absolute;
    left: 46px;
    top: 137px;
    width: 841px;
    height: 696px;
    border-radius: 50%;
    background: radial-gradient(circle at 50% 50%, var(--disc-light), var(--disc-deep));
  }
  .headline-kicker {
    position: absolute;
    top: 36px;
    left: 0;
    width: 100%;
    text-align: center;
    font-weight: 900;
    font-size: 58px;
    line-height: 1;
    letter-spacing: 3px;
    color: var(--ink-navy);
  }
  .headline-kicker .accent { color: var(--flash-yellow); }
  .title-band {
    position: absolute;
    left: 23px;
    width: 920px;
    height: 194px;
    background: var(--band-navy);
    display: flex;
    align-items: center;
    justify-content: center;
    font-weight: 700;
    line-height: 1;
    text-transform: uppercase;
  }
  .title-band--top {
    top: 227px;
    font-size: 140px;
    letter-spacing: 12px;
    padding-left: 12px;
    color: var(--paper-white);
  }
  .title-band--bottom {
    top: 600px;
    font-size: 116px;
    letter-spacing: 13px;
    padding-left: 13px;
    color: var(--deal-orange);
  }
  .terms-box {
    position: absolute;
    left: 122px;
    top: 1020px;
    width: 751px;
    height: 79px;
    border: 4px solid var(--paper-white);
    display: flex;
    align-items: center;
    justify-content: center;
    font-family: "Bebas Neue", sans-serif;
    font-size: 56px;
    line-height: 1;
    letter-spacing: 8px;
    padding-top: 4px;
    color: var(--flash-yellow);
  }
</style>
</head>
<body>
  <main class="poster">
    <div class="backdrop-scene" role="img" aria-label="Hazy aerial photo of a town at sunset under a soft lilac sky"></div>
    <div class="eye-photo" role="img" aria-label="Circular close-up photograph of the back of an eye"></div>

    <p class="headline-kicker">NOW <span class="accent">AVAILABLE*</span></p>

    <h1 class="title-band title-band--top">Two Pair</h1>
    <h2 class="title-band title-band--bottom">Packages</h2>

    <p class="terms-box">*Conditions Apply</p>
  </main>
</body>
</html>
```